Lumavento business card

We need a modern business card - With our 4 colors - See web: www.lumavento.dk

I have attached logo and som old business Cards we have - Lets Make the new ones shine...:-) -

Industry/Entity Type

Business

Requirements
Must have
• the logo with lumavento only,

```html
<!DOCTYPE html>
<html lang="da">
<head>
<meta charset="utf-8">
<title>Lumavento visitkort</title>
<link rel="stylesheet" href="https://fonts.googleapis.com/css2?family=Montserrat:wght@400;600&family=Open+Sans:wght@400;600&display=swap">
<style>
  :root {
    --bg: #ecebe8;
    --white: #ffffff;
    --ink: #1a1a1a;
    --lime: #8dc63f;
    --purple: #8a3ca0;
    --magenta: #e03ab0;
    --green: #a6d86a;
    --orange: #f0955a;
  }
  * { box-sizing: border-box; margin: 0; padding: 0; }
  html, body { width: 1200px; height: 900px; overflow: hidden; }
  body {
    background: var(--bg);
    font-family: "Open Sans", Arial, sans-serif;
    position: relative;
  }
  .card {
    position: absolute;
    top: 300px;
    width: 520px;
    height: 300px;
    overflow: hidden;
    box-shadow: 0 6px 18px rgba(0,0,0,.18);
  }
  .card--back { left: 50px; }
  .card--front { left: 630px; background: var(--white); }

  .colour-field {
    position: absolute;
    inset: 0;
    background: linear-gradient(90deg, var(--purple) 0%, var(--magenta) 35%, var(--green) 65%, var(--orange) 100%);
  }

  .back-identity {
    position: absolute;
    left: 0; right: 0; top: 62px;
    text-align: center;
    color: var(--white);
    font-family: "Montserrat", Arial, sans-serif;
  }
  .back-identity__brand {
    font-size: 34px;
    font-weight: 600;
    letter-spacing: 2px;
    margin-bottom: 26px;
  }
  .back-identity__name,
  .back-identity__title {
    font-size: 17px;
    letter-spacing: 2.5px;
    width: 270px;
    margin: 0 auto;
    padding: 4px 0;
  }
  .back-identity__name { border-bottom: 2px solid var(--white); }

  .front-top {
    height: 168px;
    text-align: center;
    padding-top: 46px;
  }
  .front-brand {
    font-family: "Montserrat", Arial, sans-serif;
    font-size: 26px;
    font-weight: 600;
    letter-spacing: 3px;
    color: var(--lime);
    display: inline-flex;
    align-items: center;
    gap: 10px;
  }
  .front-brand__dot {
    width: 14px; height: 14px; border-radius: 50%;
    background: var(--lime);
  }
  .front-rule {
    width: 250px; height: 2px; background: var(--lime);
    margin: 10px auto 6px;
  }
  .front-tagline { font-size: 11px; color: var(--ink); }
  .front-band-line {
    height: 4px; background: var(--lime);
  }
  .front-bottom {
    position: absolute;
    left: 0; right: 0; bottom: 0;
    height: 122px;
  }
  .contact {
    position: absolute;
    top: 18px;
    color: var(--ink);
    font-size: 14px;
    line-height: 24px;
  }
  .contact--reach { right: 268px; text-align: right; }
  .contact--reach li {
    list-style: none;
    display: flex; align-items: center; justify-content: flex-end; gap: 8px;
  }
  .contact--reach svg { width: 13px; height: 13px; fill: var(--ink); }
  .contact--person { left: 275px; top: 8px; font-size: 12.5px; line-height: 17px; }
  .contact__name { font-size: 17px; font-weight: 600; line-height: 22px; }
  .contact__title { margin-bottom: 10px; }
</style>
</head>
<body>

<div class="card card--back">
  <div class="colour-field" role="img" aria-label="Dekorativt farvemønster i lilla, magenta, grøn og orange"></div>
  <div class="back-identity">
    <div class="back-identity__brand">lumavento</div>
    <div class="back-identity__name">Jonas Vesterby</div>
    <div class="back-identity__title">Salgsdirektør</div>
  </div>
</div>

<div class="card card--front">
  <div class="front-top">
    <div class="front-brand"><span class="front-brand__dot"></span>lumavento</div>
    <div class="front-rule"></div>
    <div class="front-tagline">Medier til unge</div>
  </div>
  <div class="front-band-line"></div>
  <div class="front-bottom">
    <div class="colour-field" role="img" aria-label="Dekorativt farvemønster i lilla, magenta, grøn og orange"></div>
    <ul class="contact contact--reach">
      <li>+45 40 12 34 56
        <svg viewBox="0 0 24 24" aria-hidden="true"><path d="M6.6 10.8a15 15 0 0 0 6.6 6.6l2.2-2.2a1 1 0 0 1 1-.25 11.4 11.4 0 0 0 3.6.57 1 1 0 0 1 1 1V20a1 1 0 0 1-1 1A17 17 0 0 1 3 4a1 1 0 0 1 1-1h3.5a1 1 0 0 1 1 1c0 1.25.2 2.45.57 3.57a1 1 0 0 1-.25 1z"/></svg>
      </li>
      <li>jv@lumavento.dk
        <svg viewBox="0 0 24 24" aria-hidden="true"><path d="M2 5h20v14H2z M4 7v.5l8 5 8-5V7l-8 5z" fill-rule="evenodd"/></svg>
      </li>
      <li>www.lumavento.dk
        <svg viewBox="0 0 24 24" aria-hidden="true"><circle cx="12" cy="12" r="10"/><path d="M2 12h20M12 2c3 3 3 17 0 20M12 2c-3 3-3 17 0 20" stroke="#fff" stroke-width="1.5" fill="none"/></svg>
      </li>
    </ul>
    <div class="contact contact--person">
      <div class="contact__name">Jonas Vesterby</div>
      <div class="contact__title">Salgsdirektør</div>
      <div>Solsikkevej 14 - 2000</div>
      <div>Frederiksberg - Tlf. 38 00 41 72</div>
    </div>
  </div>
</div>

</body>
</html>
```